Website Revamp: Bravoly.com

Just got a new logo looking for a web design to go with the business. I need the photoshop files and stock photos. No Word Press Please.

```html
<!DOCTYPE html>
<html lang="en">
<head>
<meta charset="utf-8">
<title>Bravoly</title>
<link href="https://fonts.googleapis.com/css2?family=Open+Sans:wght@400;600;700&display=swap" rel="stylesheet">
<style>
:root{
  --green:#74b530;
  --grey-btn:#6b7274;
  --text:#444;
  --nav:#555;
  --dark:#2a2a2a;
  --band:#3a3c40;
  --white:#fff;
}
*{box-sizing:border-box;margin:0;padding:0}
html,body{width:1200px;height:2533px;overflow:hidden}
body{position:relative;font-family:'Open Sans',sans-serif;color:var(--text);background:var(--white)}
.abs{position:absolute}
.brand{left:144px;top:30px;display:flex;align-items:center;gap:12px}
.brand-dot{width:44px;height:44px;border-radius:50%;background:var(--green)}
.brand-name{font-size:34px;font-weight:700;color:var(--green);letter-spacing:1px}
.search{left:553px;top:35px;width:239px;height:39px;border:1px solid #bbb;font-size:13px;color:#888;padding:11px 15px}
.search svg{position:absolute;right:12px;top:10px}
.hours{right:144px;top:29px;font-size:13px;color:#333}
.phone{right:144px;top:48px;font-size:28px;font-weight:600;color:#333;display:flex;align-items:center;gap:10px}
.nav{right:144px;top:109px;display:flex;gap:38px;font-size:14.5px;color:var(--nav);text-transform:uppercase}
.nav .active{color:var(--green)}
.hero{left:0;top:156px;width:1200px;height:459px;background:linear-gradient(180deg,#77736f 0%,#4c4c4e 45%,#6f6b63 100%)}
.hero-title{left:0;top:346px;width:1200px;text-align:center;color:var(--white);font-size:33px;font-weight:700;line-height:40px;text-transform:uppercase}
.arrow{width:44px;height:44px;border-radius:50%;background:var(--green);top:363px}
.h2{font-size:33px;font-weight:700;color:var(--green);text-transform:uppercase;line-height:44px}
.body-text{font-size:13.5px;line-height:27.2px;color:var(--text);letter-spacing:-0.1px}
.btn{display:inline-block;background:var(--grey-btn);color:var(--white);font-size:13.5px;font-weight:700;text-transform:uppercase;height:39px;line-height:39px;padding:0 14px}
.welcome{left:144px;top:700px;width:440px}
.welcome .body-text{margin-top:18px}
.welcome .btn{margin-top:14px}
.frame{background:var(--green)}
.photo-video{left:638px;top:696px;width:410px;height:271px;background:linear-gradient(160deg,#6f7f90,#3d4046 60%,#5a4a3c)}
.play{left:823px;top:812px;width:48px;height:48px;border-radius:50%;background:var(--white)}
.band{left:0;top:1056px;width:1200px;height:414px;background:linear-gradient(180deg,#3d3f43,#2f3033)}
.service{width:280px;text-align:center;top:1135px}
.service h3{font-size:24px;font-weight:700;color:var(--green);text-transform:uppercase;margin-top:30px}
.service p{font-size:12px;line-height:22.5px;color:var(--white);margin-top:6px}
.service .btn{margin-top:14px}
.photo-parts{left:152px;top:1550px;width:410px;height:272px;background:linear-gradient(135deg,#4a3f36,#2b2724 55%,#5d4634)}
.checks{left:632px;top:1618px;display:grid;grid-template-columns:265px 170px;row-gap:5px;font-size:14px;color:var(--text)}
.checks li{list-style:none;display:flex;align-items:center;gap:9px;height:22px;white-space:nowrap}
.map{left:0;top:1910px;width:1200px;height:480px;background:linear-gradient(180deg,#dcdcdc,#cfcfcf)}
.info-bar{left:144px;top:2359px;width:912px;height:63px;background:var(--green);color:var(--white);font-size:20px;display:flex;align-items:center;justify-content:center;gap:18px}
.info-bar span{display:flex;align-items:center;gap:6px}
.footer{left:0;top:2390px;width:1200px;height:143px;background:var(--dark)}
.foot-links{left:143px;top:2451px;font-size:12px;color:#bbb;word-spacing:2px}
.copy{left:143px;top:2483px;font-size:12px;color:#bbb}
.social{top:2462px;width:28px;height:28px;border-radius:50%;background:#999}
</style>
</head>
<body>

<header>
  <div class="abs brand"><span class="brand-dot"></span><span class="brand-name">BRAVOLY</span></div>
  <div class="abs search">Search auto parts
    <svg width="16" height="16" viewBox="0 0 16 16"><circle cx="6.5" cy="6.5" r="4.5" fill="none" stroke="#74b530" stroke-width="2.5"/><line x1="10" y1="10" x2="14" y2="14" stroke="#74b530" stroke-width="3"/></svg>
  </div>
  <div class="abs hours">Mon-Fri 8t a.m - 5 p.m / Sat - Sun Closed</div>
  <div class="abs phone">
    <svg width="22" height="22" viewBox="0 0 24 24"><path d="M6.6 10.8a15 15 0 0 0 6.6 6.6l2.2-2.2c.3-.3.7-.4 1-.2 1.1.4 2.3.6 3.6.6.6 0 1 .4 1 1V20c0 .6-.4 1-1 1A17 17 0 0 1 3 4c0-.6.4-1 1-1h3.5c.6 0 1 .4 1 1 0 1.3.2 2.5.6 3.6.1.3 0 .7-.2 1z" fill="#333"/></svg>
    456 213 7790
  </div>
  <nav class="abs nav">
    <span class="active">Home</span><span>About Us</span><span>Recycling</span><span>Sell Your Car</span><span>Inventory</span><span>Contact Us</span>
  </nav>
</header>

<section>
  <div class="abs hero" role="img" aria-label="Photo of scrapped cars stacked on racks in a salvage yard"></div>
  <h1 class="abs hero-title">Pellentesque accumsan<br>metus elementum</h1>
  <div class="abs arrow" style="left:51px"><svg width="44" height="44" viewBox="0 0 44 44"><polyline points="25,13 16,22 25,31" fill="none" stroke="#fff" stroke-width="3.5"/></svg></div>
  <div class="abs arrow" style="left:1103px"><svg width="44" height="44" viewBox="0 0 44 44"><polyline points="19,13 28,22 19,31" fill="none" stroke="#fff" stroke-width="3.5"/></svg></div>
</section>

<section>
  <div class="abs welcome">
    <h2 class="h2">Welcome to Bravoly</h2>
    <p class="body-text">Integer ac ante neque. Vestibulum a eleifend sapien, at consectetur risus. Nulla finibus lacinia dolor, semper dictum leo eleifend non. Etiam non nulla non turpis pharetra tincidunt sed ut lorem. Etiam bibendum eros at velit consectetur commodo. Ut auctor convallis ligula a finibus. Fusce lacinia rutrum nunc at vulputate.</p>
    <span class="btn">Read More</span>
  </div>
  <div class="abs frame" style="left:646px;top:704px;width:410px;height:271px"></div>
  <div class="abs photo-video" role="img" aria-label="Video still of a crane grabber lifting a scrapped car"></div>
  <div class="abs play"><svg width="48" height="48" viewBox="0 0 48 48"><polygon points="19,14 34,24 19,34" fill="#111"/></svg></div>
</section>

<section>
  <div class="abs band" role="img" aria-label="Dark-tinted photo of a yard full of scrapped cars"></div>
  <div class="abs service" style="left:137px">
    <svg width="80" height="80" viewBox="0 0 80 80"><circle cx="40" cy="40" r="36" fill="none" stroke="#fff" stroke-width="3"/><rect x="20" y="32" width="40" height="18" rx="3" fill="none" stroke="#fff" stroke-width="3"/><circle cx="29" cy="52" r="5" fill="none" stroke="#fff" stroke-width="3"/><circle cx="51" cy="52" r="5" fill="none" stroke="#fff" stroke-width="3"/></svg>
    <h3>Auto Recycling</h3>
    <p>Etiam bibendum eros velit consectetur commodo. Ut auctor convallis ligula a finibus. Fusce lacinia rutrum nunc at vulputate.</p>
    <span class="btn">Read More</span>
  </div>
  <div class="abs service" style="left:460px">
    <svg width="80" height="80" viewBox="0 0 80 80"><rect x="14" y="40" width="52" height="22" rx="4" fill="none" stroke="#fff" stroke-width="3"/><rect x="22" y="18" width="36" height="18" fill="none" stroke="#fff" stroke-width="3"/><circle cx="26" cy="64" r="5" fill="none" stroke="#fff" stroke-width="3"/><circle cx="54" cy="64" r="5" fill="none" stroke="#fff" stroke-width="3"/></svg>
    <h3>Sell Your Car</h3>
    <p>Etiam bibendum eros velit consectetur commodo. Ut auctor convallis ligula a finibus. Fusce lacinia rutrum nunc at vulputate.</p>
    <span class="btn">Read More</span>
  </div>
  <div class="abs service" style="left:782px">
    <svg width="80" height="80" viewBox="0 0 80 80"><rect x="18" y="24" width="44" height="42" rx="3" fill="none" stroke="#fff" stroke-width="3"/><rect x="28" y="12" width="24" height="12" fill="none" stroke="#fff" stroke-width="3"/><polyline points="44,32 36,46 46,46 38,60" fill="none" stroke="#fff" stroke-width="3"/></svg>
    <h3>Auto Parts</h3>
    <p>Etiam bibendum eros velit consectetur commodo. Ut auctor convallis ligula a finibus. Fusce lacinia rutrum nunc at vulputate.</p>
    <span class="btn">Read More</span>
  </div>
</section>

<section>
  <div class="abs frame" style="left:144px;top:1558px;width:410px;height:272px"></div>
  <div class="abs photo-parts" role="img" aria-label="Photo of a pile of rusty gears and engine parts"></div>
  <h2 class="abs h2" style="left:632px;top:1558px">Why choose Bravoly</h2>
  <ul class="abs checks">
    <li><svg width="12" height="10" viewBox="0 0 12 10"><polyline points="1,5 4.5,8.5 11,1.5" fill="none" stroke="#74b530" stroke-width="2.5"/></svg>Pellentesque habitant morbi</li>
    <li><svg width="12" height="10" viewBox="0 0 12 10"><polyline points="1,5 4.5,8.5 11,1.5" fill="none" stroke="#74b530" stroke-width="2.5"/></svg>Quisque arcu erat</li>
    <li><svg width="12" height="10" viewBox="0 0 12 10"><polyline points="1,5 4.5,8.5 11,1.5" fill="none" stroke="#74b530" stroke-width="2.5"/></svg>Interdum malesuada fames</li>
    <li><svg width="12" height="10" viewBox="0 0 12 10"><polyline points="1,5 4.5,8.5 11,1.5" fill="none" stroke="#74b530" stroke-width="2.5"/></svg>Etiam bibendum eros</li>
    <li><svg width="12" height="10" viewBox="0 0 12 10"><polyline points="1,5 4.5,8.5 11,1.5" fill="none" stroke="#74b530" stroke-width="2.5"/></svg>Sed porttitor rutrum</li>
    <li><svg width="12" height="10" viewBox="0 0 12 10"><polyline points="1,5 4.5,8.5 11,1.5" fill="none" stroke="#74b530" stroke-width="2.5"/></svg>Nam leo est aliquam</li>
    <li><svg width="12" height="10" viewBox="0 0 12 10"><polyline points="1,5 4.5,8.5 11,1.5" fill="none" stroke="#74b530" stroke-width="2.5"/></svg>Pellentesque habitant morbi</li>
    <li><svg width="12" height="10" viewBox="0 0 12 10"><polyline points="1,5 4.5,8.5 11,1.5" fill="none" stroke="#74b530" stroke-width="2.5"/></svg>Interdum malesuada</li>
    <li><svg width="12" height="10" viewBox="0 0 12 10"><polyline points="1,5 4.5,8.5 11,1.5" fill="none" stroke="#74b530" stroke-width="2.5"/></svg>Maecenas efficitur diam</li>
    <li><svg width="12" height="10" viewBox="0 0 12 10"><polyline points="1,5 4.5,8.5 11,1.5" fill="none" stroke="#74b530" stroke-width="2.5"/></svg>Vestibulum enim dolor</li>
  </ul>
  <span class="abs btn" style="left:632px;top:1772px">Read More</span>
</section>

<section>
  <div class="abs map" role="img" aria-label="Grey street map of the city with a river, showing the business location"></div>
  <svg class="abs" style="left:609px;top:2132px" width="26" height="40" viewBox="0 0 26 40"><path d="M13 0C5.8 0 0 5.8 0 13c0 9.8 13 27 13 27s13-17.2 13-27C26 5.8 20.2 0 13 0z" fill="#74b530"/><circle cx="13" cy="13" r="5" fill="#fff"/></svg>
  <div class="abs footer"></div>
  <div class="abs info-bar">
    <span><svg width="12" height="18" viewBox="0 0 12 18"><path d="M6 0C2.7 0 0 2.7 0 6c0 4.5 6 12 6 12s6-7.5 6-12C12 2.7 9.3 0 6 0z" fill="#fff"/><circle cx="6" cy="6" r="2.2" fill="#74b530"/></svg>24 Building name, Street name, City Zipcode</span>
    <span>|</span>
    <span><svg width="17" height="17" viewBox="0 0 24 24"><path d="M6.6 10.8a15 15 0 0 0 6.6 6.6l2.2-2.2c.3-.3.7-.4 1-.2 1.1.4 2.3.6 3.6.6.6 0 1 .4 1 1V20c0 .6-.4 1-1 1A17 17 0 0 1 3 4c0-.6.4-1 1-1h3.5c.6 0 1 .4 1 1 0 1.3.2 2.5.6 3.6.1.3 0 .7-.2 1z" fill="#fff"/></svg>456 213 7790</span>
    <span>|</span>
    <span><svg width="19" height="14" viewBox="0 0 19 14"><rect x="0" y="0" width="19" height="14" rx="1.5" fill="#fff"/><polyline points="1,1.5 9.5,8 18,1.5" fill="none" stroke="#74b530" stroke-width="1.6"/></svg>info@bravoly.com</span>
  </div>
  <div class="abs foot-links">Home &nbsp;| &nbsp;About Us &nbsp;| &nbsp;Recycling &nbsp;| &nbsp;Sell Your Car &nbsp;| &nbsp;Inventory &nbsp;| &nbsp;Contact Us</div>
  <div class="abs copy">Copyright © 2020 &nbsp;Bravoly. &nbsp;All rights reserved.</div>
  <div class="abs social" style="left:977px"></div>
  <div class="abs social" style="left:1028px"></div>
</section>

</body>
</html>
```